VIP Card Design Project

uZorvo is a premium sneaker store selling brand name sneakers like Volta, Rexa, Kembro and etc. ( www.uzorvoshop.com ) We need to design a VIP card to promote one of our discount program called "Uzorvo VIP Band 17", which offers 24% discount off all full-priced items. The idea is because we have a "Peakline Gym center" (peaklinegym.com) next door and we are trying to design a discount program for people going to the fitness center.
The design is for the front of the card. The back will be black and white with benefits information and member information.
The front design need to include our logo, "VIP", "Band 17" and our web address "Uzorvo.com" and Chatterly and quibbr logo.
It will be a plastic card in the size of 3.375x2.125 (bleed size 3.5x2.25)

```html
<!DOCTYPE html>
<html lang="en">
<head>
<meta charset="utf-8">
<title>Uzorvo VIP Band 17 – Member Card</title>
<link href="https://fonts.googleapis.com/css2?family=Alfa+Slab+One&family=Arimo:wght@400;700&display=swap" rel="stylesheet">
<style>
  :root {
    --bg: #ece8e2;
    --card: #ffffff;
    --frame: #c9c9c9;
    --frame-inner: #e4e4e4;
    --green: #3aaa35;
    --green-dark: #2f8f2c;
    --red: #e0141b;
    --grey-text: #555555;
    --muted: #8a8a8a;
    --band: #d8d8d8;
    --band-light: #f1f1f1;
  }
  * { box-sizing: border-box; margin: 0; padding: 0; }
  html, body { width: 1200px; height: 665px; overflow: hidden; }
  body { background: var(--bg); font-family: "Arimo", Arial, sans-serif; position: relative; }

  .card {
    position: absolute; top: 158px; width: 540px; height: 340px;
    background: var(--card);
    border: 12px solid var(--frame-inner);
    outline: 2px solid var(--frame);
    box-shadow: 0 6px 18px rgba(0,0,0,.18);
    overflow: hidden;
  }
  .card--front { left: 40px; }
  .card--back { left: 620px; }

  /* Front */
  .corner-band { position: absolute; left: 0; top: 0; width: 170px; height: 316px; }
  .brand-vertical {
    position: absolute; left: 28px; top: 290px; transform: rotate(-90deg); transform-origin: left top;
    font-family: "Alfa Slab One", Georgia, serif; font-size: 46px; line-height: 1; color: var(--green);
    letter-spacing: 1px; white-space: nowrap;
  }
  .product-photo {
    position: absolute; right: 10px; width: 120px; height: 90px; border-radius: 4px;
  }
  .photo-1 { top: 6px; background: linear-gradient(135deg, #d6d0c4, #c2362e 55%, #2a2a2a); }
  .photo-2 { top: 110px; background: linear-gradient(135deg, #7a2a1e, #e9dcc0 50%, #3b6fb0); }
  .photo-3 { top: 214px; background: linear-gradient(135deg, #b08a55, #f2efe9 50%, #d7392c); }
  .burst { position: absolute; left: 278px; top: 44px; width: 92px; height: 92px; }
  .burst-label {
    position: absolute; left: 278px; top: 72px; width: 92px; text-align: center;
    font-family: "Arimo", Arial, sans-serif; font-weight: 700; font-size: 28px; color: #fff;
  }
  .discount-line {
    position: absolute; right: 150px; top: 140px; text-align: right; white-space: nowrap;
    font-family: "Alfa Slab One", Georgia, serif; color: var(--red); font-size: 15px; line-height: 1.15;
    transform: rotate(-14deg); transform-origin: right top;
  }
  .club-title {
    position: absolute; left: 100px; top: 236px; white-space: nowrap;
    font-family: "Alfa Slab One", Georgia, serif; font-weight: 400; font-size: 21px; color: var(--green);
  }
  .web-address {
    position: absolute; left: 120px; top: 282px; font-size: 12px; color: var(--muted);
    display: flex; align-items: center; gap: 5px;
  }
  .web-address .dot { width: 10px; height: 10px; border-radius: 50%; border: 1.5px solid var(--muted); }
  .social { position: absolute; left: 268px; top: 282px; display: flex; gap: 8px; font-size: 10px; color: var(--grey-text); }
  .social span { display: flex; align-items: center; gap: 4px; }
  .social i { display: inline-block; width: 10px; height: 10px; background: #6aa6d8; }

  /* Back */
  .brand-corner {
    position: absolute; right: 12px; top: 8px;
    font-family: "Alfa Slab One", Georgia, serif; font-size: 22px; color: var(--green);
  }
  .benefits { position: absolute; left: 22px; top: 44px; right: 18px; color: var(--grey-text); font-size: 11.5px; line-height: 1.3; }
  .benefits h2 { color: var(--red); font-size: 16px; font-weight: 700; margin-bottom: 8px; }
  .benefits p { margin-bottom: 8px; }
  .benefits ol { list-style: none; }
  .benefits li { display: flex; gap: 8px; margin-bottom: 9px; padding-left: 4px; }
  .benefits li b { color: var(--red); font-weight: 400; min-width: 12px; }
  .member-field {
    position: absolute; color: var(--green); font-size: 13px; display: flex; align-items: flex-end; gap: 4px;
  }
  .member-field span.rule { border-bottom: 1px dotted var(--muted); display: inline-block; height: 12px; }
  .field-name { left: 60px; bottom: 14px; }
  .field-name .rule { width: 170px; }
  .field-id { right: 18px; bottom: 46px; }
  .field-id .rule { width: 90px; }
</style>
</head>
<body>
  <section class="card card--front" aria-label="Card front">
    <svg class="corner-band" viewBox="0 0 170 316" aria-hidden="true">
      <polygon points="0,0 70,0 170,316 0,316" fill="var(--band-light)"/>
      <polygon points="0,0 40,0 120,316 0,316" fill="var(--band)"/>
    </svg>
    <div class="brand-vertical">uZorvo</div>

    <div class="product-photo photo-1" role="img" aria-label="Photo of red and black Volta running sneakers"></div>
    <div class="product-photo photo-2" role="img" aria-label="Photo of a white, blue and red Solvair basketball sneaker"></div>
    <div class="product-photo photo-3" role="img" aria-label="Photo of a white and red Trendo high-top sneaker on a court"></div>

    <svg class="burst" viewBox="0 0 100 100" aria-hidden="true">
      <polygon fill="var(--green-dark)" points="50,0 56,12 68,4 70,18 84,14 80,28 95,30 86,42 100,50 86,58 95,70 80,72 84,86 70,82 68,96 56,88 50,100 44,88 32,96 30,82 16,86 20,72 5,70 14,58 0,50 14,42 5,30 20,28 16,14 30,18 32,4 44,12"/>
    </svg>
    <div class="burst-label">24%</div>
    <div class="discount-line">discount off<br>all full-priced items.</div>

    <h1 class="club-title">Uzorvo VIP Band 17</h1>
    <div class="web-address"><span class="dot"></span>www.Uzorvo.com</div>
    <div class="social">
      <span><i></i>quibbr</span>
      <span><i></i>Chatterly</span>
    </div>
  </section>

  <section class="card card--back" aria-label="Card back">
    <div class="brand-corner">uZorvo</div>
    <div class="benefits">
      <h2>-: Benefits :-</h2>
      <p>The UZORVO Member Program entitles Members to the following benefits:</p>
      <ol>
        <li><b>a.</b><span>20% OFF your entire first purchase after you sign up (Limited Time Offer). Certain items are excluded from this offer. Please see stores for details.</span></li>
        <li><b>b.</b><span>10% OFF every purchase while being a member. Certain items are excluded from this offer. Please see stores for details.</span></li>
        <li><b>c.</b><span>Additional 10% OFF and FREE SHIPPING when an item is out of stock in store but can be shipped to you from another location.</span></li>
        <li><b>d.</b><span>Eligible to purchase exclusive items offered to members only. Purchasing of exclusive items is limited to 1 item per member per 30 days. Please see stores for details.</span></li>
      </ol>
    </div>
    <div class="member-field field-id">Member ID : <span class="rule"></span></div>
    <div class="member-field field-name">Member Name : <span class="rule"></span></div>
  </section>
</body>
</html>
```